New Business Card Design Project

We require a business card design for Vexalund, a newly established Indian company.
Our focus is on the development, manufacturing, and export of a diverse array of pharmaceutical products on a global scale. The card should convey a professional appearance, as our primary markets are in Africa, China, and Southeast Asian nations.
We envision a two-sided business card, with the reverse side dedicated to a logo set against a solid color or an elegantly designed pattern. The corners should be rounded. We would appreciate seeing both horizontal and vertical design options. We trust the designer to utilize their expertise in creating this design.

The content for the business card is included in the attached Word file.

Target Market(s)

Our primary markets are in Africa, China, and Southeast Asian, Latin America, Maldives, Sri Lanka

Industry/Entity Type

Pharmaceutical Manufacturing and Export

Contact Information for Business Card

Colors

Designer to choose colors to be used in the design.

Requirements
Must have
• The reverse side of the business card features solely the logo along with the tagline, "Care in Every Dose."
Should not have
• The logo should not exceed two instances, encompassing both the front and back sides of the card.

```html
<!DOCTYPE html>
<html lang="en">
<head>
<meta charset="UTF-8">
<title>Vexalund – Business Card</title>
<link href="https://fonts.googleapis.com/css2?family=Lexend:wght@400;600;700&display=swap" rel="stylesheet">
<style>
  :root {
    --stage: #e9e6e1;
    --blue: #2596d1;
    --blue-deep: #0b4a6a;
    --blue-mid: #1a86bb;
    --red: #e85a4a;
    --ink: #3a3d42;
    --white: #ffffff;
  }
  * { margin: 0; padding: 0; box-sizing: border-box; }
  html, body {
    width: 1200px; height: 900px; overflow: hidden;
    background: var(--stage);
    font-family: "Lexend", sans-serif;
  }
  .stage {
    width: 1200px; height: 900px;
    display: flex; flex-direction: column;
    align-items: center; justify-content: center; gap: 44px;
  }
  .card {
    position: relative;
    width: 600px; height: 343px;
    border-radius: 30px;
    overflow: hidden;
    box-shadow: 0 10px 28px rgba(0,0,0,0.18);
  }

  /* Reverse side */
  .card-back {
    background: radial-gradient(ellipse at 50% 45%, var(--blue) 0%, var(--blue-mid) 35%, var(--blue-deep) 100%);
    color: var(--white);
  }
  .card-back .brand {
    position: absolute; top: 118px; left: 0; width: 100%;
    text-align: center;
    font-weight: 600; font-size: 54px; letter-spacing: 0.5px;
  }
  .card-back .rule {
    position: absolute; top: 200px; left: 90px; width: 420px; height: 1px;
    background: rgba(255,255,255,0.85);
  }
  .card-back .tagline {
    position: absolute; top: 214px; left: 0; width: 100%;
    text-align: center; font-weight: 400; font-size: 17px; letter-spacing: 0.4px;
  }

  /* Front side */
  .card-front { background: linear-gradient(135deg, #f1f1f1 0%, var(--white) 55%, var(--white) 100%); }
  .card-front .brand {
    position: absolute; top: 78px; right: 44px;
    font-weight: 600; font-size: 50px; color: var(--blue); letter-spacing: 0.5px;
  }
  .card-front .rule {
    position: absolute; top: 160px; left: 240px; width: 325px; height: 1px;
    background: var(--red);
  }
  .holder { position: absolute; left: 40px; top: 146px; }
  .holder-name { font-weight: 600; font-size: 19px; color: var(--blue); text-transform: uppercase; white-space: nowrap; }
  .holder-role { font-weight: 400; font-size: 15px; color: var(--red); margin-top: 2px; }
  .contacts { position: absolute; left: 40px; top: 210px; list-style: none; }
  .contacts li {
    display: flex; align-items: center; gap: 10px;
    font-size: 14px; color: var(--ink); height: 26px; white-space: nowrap;
  }
  .contacts svg { width: 16px; height: 16px; flex: none; }
</style>
</head>
<body>
<main class="stage">
  <section class="card card-back" aria-label="Reverse side">
    <div class="brand">Vexalund</div>
    <div class="rule"></div>
    <div class="tagline">Care in Every Dose</div>
  </section>

  <section class="card card-front" aria-label="Front side">
    <div class="brand">Vexalund</div>
    <div class="rule"></div>
    <div class="holder">
      <div class="holder-name">Arjun K. Mehra</div>
      <div class="holder-role">CEO Of Vexalund</div>
    </div>
    <ul class="contacts">
      <li>
        <svg viewBox="0 0 16 16" aria-hidden="true"><rect x="4" y="1" width="8" height="14" rx="1.5" fill="none" stroke="#e85a4a" stroke-width="1.5"/><circle cx="8" cy="12.5" r="0.9" fill="#e85a4a"/></svg>
        +919876543210
      </li>
      <li>
        <svg viewBox="0 0 16 16" aria-hidden="true"><rect x="1" y="3" width="14" height="10" rx="1" fill="#e85a4a"/><path d="M1.5 3.5 L8 9 L14.5 3.5" fill="none" stroke="#fff" stroke-width="1.3"/></svg>
        amehra@vexalund.com
      </li>
      <li>
        <svg viewBox="0 0 16 16" aria-hidden="true"><g fill="none" stroke="#e85a4a" stroke-width="1.2"><circle cx="8" cy="8" r="6.5"/><ellipse cx="8" cy="8" rx="3" ry="6.5"/><path d="M1.5 8h13M2.5 4.7h11M2.5 11.3h11"/></g></svg>
        www.vexalund.com
      </li>
      <li>
        <svg viewBox="0 0 16 16" aria-hidden="true"><path d="M8 15 C8 15 2.5 9.5 2.5 6 A5.5 5.5 0 0 1 13.5 6 C13.5 9.5 8 15 8 15Z" fill="#e85a4a"/><circle cx="8" cy="6" r="2" fill="#fff"/></svg>
        14, Lotus Nagar, Nashik, 422005, India
      </li>
    </ul>
  </section>
</main>
</body>
</html>
```